SkyvornQ Business Cards and Stationary Design

Need a design for our business cards and stationary. I want to carry on the theme of the logo. I want the business cards to have a design on the back. I would like the business cards and the stationary to carry the same theme, design scheme, and branding

Target Market(s)

Airlines and Maintenance Facilities

Industry/Entity Type

Aviation

Contact Information for Business Card

Name
Position Title
Address: 4827 Trellis Hollow Road, Fort Pierce, Florida, 34951
Office Number
Mobile Number
Email
Website

Font styles to use
Serif
Sans Serif

Colors

Designer to choose colors to be used in the design.

```html
<!DOCTYPE html>
<html lang="en">
<head>
<meta charset="utf-8">
<title>SkyvornQ Business Card</title>
<link rel="stylesheet" href="https://fonts.googleapis.com/css2?family=Michroma&family=Open+Sans:wght@400;600;700&display=swap">
<style>
  :root {
    --backdrop: #3b3b3d;
    --card-black: #1e1f22;
    --emboss: #4a4c51;
    --sky: #1fa3e8;
    --navy: #12336b;
    --navy-deep: #0d2a5a;
    --slate: #3a3d43;
    --white: #f2f4f7;
    --muted: #c9ccd2;
  }
  * { margin: 0; padding: 0; box-sizing: border-box; }
  html, body {
    width: 799px; height: 1200px; overflow: hidden;
    background: var(--backdrop);
  }
  .sheet {
    position: relative; width: 799px; height: 1200px;
    display: flex; flex-direction: column; align-items: center;
    justify-content: space-around; padding: 70px 0;
  }
  .card {
    position: relative; width: 660px; height: 378px;
    border-radius: 20px; overflow: hidden;
    background: var(--card-black);
    box-shadow: 0 14px 30px rgba(0,0,0,.45);
  }
  /* front */
  .card-front { display: flex; align-items: center; justify-content: center; }
  .front-brand {
    display: flex; flex-direction: column; align-items: center; gap: 22px;
  }
  .front-brand .brand-dot {
    width: 70px; height: 70px; border-radius: 50%;
    border: 3px solid var(--emboss);
  }
  .front-brand .brand-name {
    font-family: "Michroma", sans-serif; font-size: 46px;
    letter-spacing: 6px; color: var(--emboss);
  }
  /* back */
  .card-back .waves { position: absolute; inset: 0; width: 100%; height: 100%; }
  .back-brand {
    position: absolute; left: 40px; top: 34px;
    display: flex; flex-direction: column; align-items: center; gap: 12px;
  }
  .back-brand .brand-dot {
    width: 60px; height: 60px; border-radius: 50%; background: var(--sky);
  }
  .back-brand .brand-name {
    font-family: "Michroma", sans-serif; font-size: 28px;
    letter-spacing: 5px; color: var(--white);
  }
  .holder {
    position: absolute; right: 40px; top: 66px; text-align: right;
    font-family: "Open Sans", sans-serif;
  }
  .holder .name { font-size: 24px; font-weight: 700; color: var(--white); }
  .holder .role { font-size: 15px; color: var(--sky); margin-top: 2px; }
  .holder .address { font-size: 15px; color: var(--muted); margin-top: 8px; line-height: 1.35; }
  .contacts {
    position: absolute; right: 40px; bottom: 22px;
    font-family: "Open Sans", sans-serif; font-size: 15px; color: var(--white);
    list-style: none;
  }
  .contacts li {
    display: flex; align-items: center; justify-content: flex-end;
    gap: 10px; line-height: 23px;
  }
  .contacts svg { width: 15px; height: 15px; fill: var(--sky); flex: none; }
</style>
</head>
<body>
<main class="sheet">
  <section class="card card-front" aria-label="Business card front">
    <div class="front-brand">
      <span class="brand-dot"></span>
      <span class="brand-name">SKYVORNQ</span>
    </div>
  </section>

  <section class="card card-back" aria-label="Business card back">
    <svg class="waves" viewBox="0 0 660 378" preserveAspectRatio="none" aria-hidden="true">
      <path d="M0,160 C140,250 280,262 430,250 C540,242 615,215 660,190 L660,378 L0,378 Z" fill="var(--slate)"/>
      <path d="M0,176 C130,258 270,276 420,266 C540,258 620,232 660,208 L660,378 L0,378 Z" fill="var(--sky)"/>
      <path d="M0,196 C120,272 262,292 405,284 C525,278 605,252 660,232 L660,378 L0,378 Z" fill="var(--navy)"/>
      <path d="M0,290 C150,325 330,345 660,320 L660,378 L0,378 Z" fill="var(--navy-deep)" opacity=".55"/>
    </svg>

    <div class="back-brand">
      <span class="brand-dot"></span>
      <span class="brand-name">SKYVORNQ</span>
    </div>

    <div class="holder">
      <p class="name">Marcus Delrowe</p>
      <p class="role">Managing Director</p>
      <p class="address">4827 Trellis Hollow Road,<br>Larkmoor, GA 31907</p>
    </div>

    <ul class="contacts">
      <li>2145 3098 612
        <svg viewBox="0 0 24 24"><path d="M6.6 10.8a15.1 15.1 0 0 0 6.6 6.6l2.2-2.2c.3-.3.7-.4 1-.2 1.1.4 2.3.6 3.6.6.6 0 1 .4 1 1V20c0 .6-.4 1-1 1A17 17 0 0 1 3 4c0-.6.4-1 1-1h3.5c.6 0 1 .4 1 1 0 1.3.2 2.5.6 3.6.1.3 0 .7-.2 1z"/></svg>
      </li>
      <li>8870 4412 305
        <svg viewBox="0 0 24 24"><path d="M7 1h10a2 2 0 0 1 2 2v18a2 2 0 0 1-2 2H7a2 2 0 0 1-2-2V3a2 2 0 0 1 2-2zm0 3v14h10V4zm5 15.5a1 1 0 1 0 0 2 1 1 0 0 0 0-2z"/></svg>
      </li>
      <li>marcus@skyvornq.com
        <svg viewBox="0 0 24 24"><path d="M2 5h20v14H2zm2 2v.5l8 5 8-5V7l-8 5z"/></svg>
      </li>
      <li>www.skyvornq.com
        <svg viewBox="0 0 24 24"><path d="M12 2a10 10 0 1 0 0 20 10 10 0 0 0 0-20zm6.9 6h-3a15 15 0 0 0-1.3-3.9A8 8 0 0 1 18.9 8zM12 4c.8 1.2 1.5 2.5 1.9 4h-3.8c.4-1.5 1.1-2.8 1.9-4zM4.3 14a8 8 0 0 1 0-4h3.4a16 16 0 0 0 0 4zm.8 2h3a15 15 0 0 0 1.3 3.9A8 8 0 0 1 5.1 16zm3-8h-3a8 8 0 0 1 4.3-3.9A15 15 0 0 0 8.1 8zM12 20c-.8-1.2-1.5-2.5-1.9-4h3.8c-.4 1.5-1.1 2.8-1.9 4zm2.3-6H9.7a14 14 0 0 1 0-4h4.6a14 14 0 0 1 0 4zm.3 5.9a15 15 0 0 0 1.3-3.9h3a8 8 0 0 1-4.3 3.9zm1.7-5.9a16 16 0 0 0 0-4h3.4a8 8 0 0 1 0 4z"/></svg>
      </li>
    </ul>
  </section>
</main>
</body>
</html>
```